Luxury Wine Label for New Startup Winery

We need a wine label for our new winery startup. We have worked with a local designer but do not feel the resulting label / logo have the elevation required to present our brand as a luxury wine. Our winery is called "Quailbrook Vineyards" and we are focused on extremely high quality hand crafted artisan and estate wines from the Pacific Northwest.
We would like to see designs that utilize a tree line, or other imagery that represents the "Quailbrook" part of our company name. Another interesting feature could be wood grain.
A logo will be required based on your design so please design with this in mind:
This logo should be consistent with the wine bottle label design, and should be representative of our high end exclusive wine while giving a sense of place (Oregon/ Pacific Northwest.)
I will supply an image of the design we received from our local designer, PLEASE NOTE: in general we do like wood grain and tree line concepts but feel the execution was poorly done.
ATTN: Logo design should be suitable for use on: Bottles (Red wine/rose/white wine), Bussiness cards, vehicle signage, business signage, etc
P.S.:
If you have a design that is not outside the box we are still interested in seeing it.
Label is for a burgundy style bottle with a label height of 3.5 - 4" and a width of 3.5-4"
any label <= 4"x4" and >=3.5"x3.5" will be acceptable:
HOWEVER Width should be greater than or equal to height due to the bottle format
Target Market(s)
Wine enthusiasts with adequate discretionary budgets to afford $100 bottles of wine.
Industry/Entity Type
Wine / Winery
Requirements
Must have
- A sense of luxury, a feel of exclusivity, and a theme consistent with our product and brand name
Nice to have
- Tree line, wood grain or other wood themes. Serif fonts
Should not have
- anything cheesy, off topic, hard to read script fonts or anything that makes the label hard to read from a few feet away or too busy

```html
<!DOCTYPE html>
<html lang="en">
<head>
<meta charset="utf-8">
<title>Quailbrook Vineyards — Label Range</title>
<link rel="stylesheet" href="https://fonts.googleapis.com/css2?family=Cormorant+Garamond:wght@500;600&display=swap">
<style>
  :root {
    --canvas: #f7f6f1;
    --ink-black: #1c1b1a;
    --ink-charcoal: #2a2826;
    --gold-light: #f3d58f;
    --gold: #c9953f;
    --gold-deep: #8a5a1c;
    --olive-label: #8a6a2c;
    --olive-dark: #5e4518;
    --cream: #ece0c4;
    --cream-light: #f4ede0;
    --white-band: #efeeec;
    --silver-text: #b9b6b0;
    --dark-text: #2a2622;
    --seal-grey: #c4c2bc;
  }
  * { box-sizing: border-box; margin: 0; padding: 0; }
  html, body { width: 1200px; height: 1200px; overflow: hidden; background: var(--canvas); }
  body { font-family: "Cormorant Garamond", Georgia, serif; position: relative; }

  .brand-seal {
    position: absolute; left: 66px; top: 70px;
    display: flex; align-items: center; gap: 10px;
    color: var(--seal-grey); font-weight: 600; font-size: 15px; letter-spacing: 0.18em;
    text-transform: uppercase;
  }
  .brand-seal__circle { width: 22px; height: 22px; border-radius: 50%; background: var(--seal-grey); }

  .label-range {
    position: absolute; left: 45px; top: 380px;
    display: flex; gap: 45px;
  }
  .label {
    position: relative; width: 340px; height: 340px; overflow: hidden;
  }
  .label__wordmark {
    position: absolute; top: 34px; left: 0; right: 0; text-align: center;
  }
  .label__brand {
    display: block; font-size: 23px; font-weight: 600; letter-spacing: 0.2em; padding-left: 0.2em;
  }
  .label__sub {
    display: block; margin-top: 2px; font-size: 12px; font-weight: 600; letter-spacing: 0.42em; padding-left: 0.42em;
  }
  .label__treeline {
    position: absolute; left: 0; right: 0; top: 92px; height: 70px;
  }
  .label__variety-band {
    position: absolute; left: 0; right: 0; top: 162px; height: 66px;
    display: flex; align-items: center; justify-content: center;
  }
  .label__variety {
    font-size: 17px; font-weight: 600; letter-spacing: 0.2em; padding-left: 0.2em;
  }
  .label__woodgrain {
    position: absolute; left: 0; right: 0; top: 228px; bottom: 0;
  }

  /* Merlot */
  .label--merlot { background: var(--ink-black); }
  .label--merlot .label__brand, .label--merlot .label__sub { color: var(--gold-light); }
  .label--merlot .label__treeline { background: linear-gradient(180deg, var(--ink-black) 0%, var(--gold) 55%, var(--gold-light) 75%, var(--ink-charcoal) 100%); }
  .label--merlot .label__variety-band { background: var(--ink-charcoal); }
  .label--merlot .label__variety { color: var(--silver-text); }
  .label--merlot .label__woodgrain { background: linear-gradient(180deg, var(--gold-deep) 0%, var(--gold) 30%, var(--ink-charcoal) 60%, var(--ink-black) 80%, var(--gold) 100%); }

  /* Chardonnay */
  .label--chardonnay { background: var(--olive-label); }
  .label--chardonnay .label__brand, .label--chardonnay .label__sub { color: var(--cream-light); }
  .label--chardonnay .label__treeline { background: linear-gradient(180deg, var(--olive-label) 0%, var(--gold) 55%, var(--gold-light) 75%, var(--ink-charcoal) 100%); }
  .label--chardonnay .label__variety-band { background: var(--ink-charcoal); }
  .label--chardonnay .label__variety { color: var(--olive-label); }
  .label--chardonnay .label__woodgrain { background: linear-gradient(180deg, var(--gold-deep) 0%, var(--gold) 30%, var(--ink-charcoal) 55%, var(--olive-dark) 80%, var(--gold) 100%); }

  /* Rosé */
  .label--rose { background: var(--cream); }
  .label--rose .label__brand, .label--rose .label__sub { color: var(--gold); }
  .label--rose .label__treeline { background: linear-gradient(180deg, var(--cream) 0%, var(--gold) 55%, var(--gold-light) 80%, var(--white-band) 100%); }
  .label--rose .label__variety-band { background: var(--white-band); }
  .label--rose .label__variety { color: var(--dark-text); }
  .label--rose .label__woodgrain { background: linear-gradient(180deg, var(--gold-light) 0%, var(--cream) 35%, var(--cream-light) 65%, var(--gold) 100%); }
</style>
</head>
<body>
  <div class="brand-seal">
    <span class="brand-seal__circle"></span>
    <span>Quailbrook Vineyards</span>
  </div>

  <main class="label-range">
    <section class="label label--merlot">
      <div class="label__wordmark">
        <span class="label__brand">QUAILBROOK</span>
        <span class="label__sub">VINEYARDS</span>
      </div>
      <div class="label__treeline" role="img" aria-label="Gold foil tree line over a ridge"></div>
      <div class="label__variety-band"><span class="label__variety">MERLOT</span></div>
      <div class="label__woodgrain" role="img" aria-label="Gold foil wood grain and torn landscape layers"></div>
    </section>

    <section class="label label--chardonnay">
      <div class="label__wordmark">
        <span class="label__brand">QUAILBROOK</span>
        <span class="label__sub">VINEYARDS</span>
      </div>
      <div class="label__treeline" role="img" aria-label="Gold foil tree line over a ridge"></div>
      <div class="label__variety-band"><span class="label__variety">CHARDONNAY</span></div>
      <div class="label__woodgrain" role="img" aria-label="Gold foil wood grain and torn landscape layers"></div>
    </section>

    <section class="label label--rose">
      <div class="label__wordmark">
        <span class="label__brand">QUAILBROOK</span>
        <span class="label__sub">VINEYARDS</span>
      </div>
      <div class="label__treeline" role="img" aria-label="Gold foil tree line over a ridge"></div>
      <div class="label__variety-band"><span class="label__variety">ROSE</span></div>
      <div class="label__woodgrain" role="img" aria-label="Cream and gold wood grain and torn landscape layers"></div>
    </section>
  </main>
</body>
</html>
```